Bright Path Notes Wordpress Blog

I need to design a WordPress blog page. The name of the Blog is "Bright Path Notes". I am hoping for a simple design that is easy for me to post future posts to. I like the color teal for this. The website is brightpathnotesblog.com where I am going to write a personal blog. I don't have a logo for this, but am hoping for a header that has some swirly, but classy looking text. Easy on the eyes. The website will only have a couple of pages - the home landing page, and an about me page.

Font styles to use
Script

Colors
00a990
86cfc6
cfeae6

Requirements
Must have
• A header for the landing page of the blog. Clean layout of where the blog posts will lie.

```html
<!DOCTYPE html>
<html lang="en">
<head>
<meta charset="utf-8">
<title>Bright Path Notes</title>
<link href="https://fonts.googleapis.com/css2?family=Dancing+Script:wght@500&family=Open+Sans:wght@300;400;600;700&display=swap" rel="stylesheet">
<style>
:root{
  --teal:#1fc8cf;
  --teal-deep:#00a990;
  --teal-mid:#86cfc6;
  --teal-pale:#cfeae6;
  --wave-light:#b6f0f3;
  --wave-strong:#2fd0d8;
  --page:#f1efef;
  --panel:#ffffff;
  --side:#fafafa;
  --ink:#333333;
  --muted:#9a9a9a;
  --icon:#8a8a8a;
  --line:#ececec;
}
*{box-sizing:border-box;margin:0;padding:0}
html,body{width:1200px;height:2594px;overflow:hidden}
body{background:var(--page);font-family:"Open Sans",Arial,sans-serif;color:var(--ink);position:relative}
.abs{position:absolute}
.header-band{left:0;top:0;width:1200px;height:176px;background:linear-gradient(180deg,var(--wave-light) 0%,#8fe6ec 55%,var(--wave-strong) 100%)}
.site-title{left:133px;top:14px;font-family:"Dancing Script",cursive;font-weight:500;font-size:54px;color:#1b1b1b;white-space:nowrap}
.header-rule{left:133px;top:93px;width:666px;height:1px;background:rgba(255,255,255,.7)}
.social{left:816px;top:19px;display:flex;gap:4px}
.social span{width:42px;height:42px;border-radius:50%;background:#fff;box-shadow:0 1px 3px rgba(0,0,0,.12);display:flex;align-items:center;justify-content:center}
.nav{left:133px;top:114px;display:flex;gap:22px;font-size:13px;color:#1b1b1b}
.nav a{color:inherit;text-decoration:none}
.nav .current{text-decoration:underline}
.search{left:816px;top:121px;width:221px;height:40px;background:#fff;border-radius:2px;box-shadow:0 1px 3px rgba(0,0,0,.1);font-size:11px;color:#888;padding:12px 14px}
.search svg{position:absolute;right:12px;top:13px}
.container{left:133px;top:176px;width:934px;height:2326px;background:var(--panel)}
.hero{left:133px;top:176px;width:934px;height:398px;background:linear-gradient(180deg,#f3efe9 0%,#f1d9b8 45%,#c08a58 62%,#5f6638 80%,#3e4a2a 100%)}
.hero-title{left:600px;top:200px;font-size:35px;font-weight:700;color:#2d2d2d;letter-spacing:.5px}
.hero-sub{left:600px;top:240px;font-size:22px;font-weight:300;color:#3a3a3a}
.arrow{width:30px;height:30px;border-radius:50%;background:#fff;box-shadow:0 1px 4px rgba(0,0,0,.2);display:flex;align-items:center;justify-content:center}
.sidebar{left:807px;top:574px;width:260px;height:1928px;background:var(--side);border-left:1px solid var(--line)}
.heading{font-size:24px;font-weight:600;color:var(--teal)}
.post-img{width:638px;height:302px}
.post-date{font-size:12px;color:var(--teal)}
.post-title{font-size:17px;line-height:22px;color:#333;width:660px;font-weight:400}
.meta{display:flex;gap:28px;font-size:9.5px;color:#555;align-items:center}
.meta span{display:flex;gap:6px;align-items:center}
.excerpt{font-size:10.5px;line-height:18px;color:var(--muted);width:640px}
.share{display:flex;gap:12px}
.share span{width:20px;height:20px;background:#e6e6e6;display:flex;align-items:center;justify-content:center}
.share .first{background:#3d5a98}
.side-text{font-size:10.5px;line-height:18px;color:#8a8a8a;width:226px}
.side-rule{left:807px;width:260px;height:1px;background:var(--line)}
.contact-item{font-size:10.5px;line-height:17px;color:#555;display:flex;gap:10px}
.pop-title{font-size:11.5px;line-height:18px;color:#333;width:226px}
.pop-date{font-size:9.5px;color:#999;margin-top:2px}
.pager{left:147px;top:2430px;display:flex;gap:14px}
.pager span{width:26px;height:26px;border-radius:50%;border:1px solid #ddd;font-size:10px;color:#777;display:flex;align-items:center;justify-content:center;background:#fff}
.pager .active{background:var(--teal);border-color:var(--teal);color:#fff}
.footer-links{left:0;top:2527px;width:1200px;text-align:center;font-size:11px;color:#444}
.copyright{left:0;top:2553px;width:1200px;text-align:center;font-size:11px;color:#444}
</style>
</head>
<body>

<div class="abs header-band" role="img" aria-label="Soft teal watercolor wave header decoration"></div>

<div class="abs site-title">Bright Path Notes</div>
<div class="abs header-rule"></div>
<div class="abs social" aria-label="Social links">
  <span><svg width="14" height="11" viewBox="0 0 14 11"><rect x=".7" y=".7" width="12.6" height="9.6" fill="none" stroke="#777" stroke-width="1.3"/><path d="M1 1l6 5 6-5" fill="none" stroke="#777" stroke-width="1.3"/></svg></span>
  <span><svg width="14" height="13" viewBox="0 0 14 13"><path d="M1 1h12v8H6l-3 3V9H1z" fill="none" stroke="#777" stroke-width="1.3"/></svg></span>
  <span><svg width="14" height="12" viewBox="0 0 14 12"><path d="M7 11 1.5 5.5A3 3 0 0 1 7 2a3 3 0 0 1 5.5 3.5z" fill="#777"/></svg></span>
  <span><svg width="14" height="14" viewBox="0 0 14 14"><path d="M7 1l1.8 3.8 4.2.5-3.1 2.9.8 4.1L7 10.3 3.3 12.3l.8-4.1L1 5.3l4.2-.5z" fill="#777"/></svg></span>
  <span><svg width="14" height="14" viewBox="0 0 14 14"><path d="M6 8l2-2M5 6L3 8a2 2 0 0 0 3 3l2-2M9 8l2-2a2 2 0 0 0-3-3L6 5" fill="none" stroke="#777" stroke-width="1.4" stroke-linecap="round"/></svg></span>
</div>
<nav class="abs nav"><a class="current" href="#">Home</a><a href="#">About Maya</a><a href="#">Contact</a></nav>
<div class="abs search">Search
  <svg width="13" height="13" viewBox="0 0 13 13"><circle cx="5.5" cy="5.5" r="4" fill="none" stroke="#666" stroke-width="1.5"/><line x1="8.5" y1="8.5" x2="12" y2="12" stroke="#666" stroke-width="1.5"/></svg>
</div>

<div class="abs container"></div>

<div class="abs hero" role="img" aria-label="Photo of a woman with arms spread wide at sunset over a field"></div>
<div class="abs hero-title">DUIS POSUERE</div>
<div class="abs hero-sub">Ante ut vestibulum interdum commodo</div>
<div class="abs arrow" style="left:116px;top:305px"><svg width="8" height="10" viewBox="0 0 8 10"><path d="M6 1 2 5l4 4" fill="none" stroke="#888" stroke-width="1.5"/></svg></div>
<div class="abs arrow" style="left:1052px;top:305px"><svg width="8" height="10" viewBox="0 0 8 10"><path d="M2 1l4 4-4 4" fill="none" stroke="#888" stroke-width="1.5"/></svg></div>

<div class="abs sidebar"></div>

<h2 class="abs heading" style="left:145px;top:624px">Recent Posts</h2>

<!-- Post 1 -->
<article>
  <div class="abs post-img" style="left:147px;top:666px;background:linear-gradient(120deg,#e9e3dc 0%,#cfc6bb 40%,#8b8478 70%,#5f6a58 100%)" role="img" aria-label="Photo of a smiling man seated at a table in a bright workshop"></div>
  <div class="abs post-date" style="left:147px;top:992px">18 march, 2017</div>
  <h3 class="abs post-title" style="left:147px;top:1020px">Nam tincidunt at arcu ut congue. Sed consectetur dictum ultrices. Mauris vitae nisi nec ipsum malesuada egestas ac ac augue.</h3>
  <div class="abs meta" style="left:147px;top:1084px">
    <span><svg width="9" height="8"><path d="M1 1h7v4H4L2 7V5H1z" fill="#555"/></svg>25 Comments</span>
    <span><svg width="9" height="8"><path d="M4.5 7.5 1 4A2 2 0 0 1 4.5 1.5 2 2 0 0 1 8 4z" fill="#555"/></svg>83 Likes</span>
    <span><svg width="9" height="9"><path d="M1 1h4l3 3-4 4-3-3z" fill="#555"/></svg>Aliquam rhoncus luctus placerat. Duis posuere, ante ut vestibulum</span>
  </div>
  <p class="abs excerpt" style="left:147px;top:1108px">Proin rutrum, velit vitae pharetra cursus, mauris diam tempor libero, ut rhoncus massa lacus vel lectus. Pellentesque et nisl ac orci rhoncus porta quis in tortor. Nunc commodo diam id tristique mollis. Praesent non aliquet sem. Nulla eu vestibulum nunc. In gravida, risus in ultricies condimentum, lacus purus mattis augue.</p>
  <div class="abs share" style="left:147px;top:1176px">
    <span class="first"><svg width="10" height="9"><path d="M1 1h8v6H1z" fill="none" stroke="#fff" stroke-width="1.2"/><path d="M1 1l4 3 4-3" fill="none" stroke="#fff" stroke-width="1.2"/></svg></span>
    <span><svg width="10" height="9"><path d="M1 1h8v5H4L2 8V6H1z" fill="none" stroke="var(--icon)" stroke-width="1.2"/></svg></span>
    <span><svg width="10" height="9"><path d="M5 8.5 1.2 4.7A2 2 0 0 1 5 2a2 2 0 0 1 3.8 2.7z" fill="var(--icon)"/></svg></span>
    <span><svg width="10" height="10"><path d="M5 .5l1.3 2.8 3 .3-2.3 2 .7 3L5 7 2.3 8.6l.7-3-2.3-2 3-.3z" fill="var(--icon)"/></svg></span>
    <span><svg width="10" height="10"><path d="M4 6l2-2M3.5 4.5 2 6a1.5 1.5 0 0 0 2 2l1.5-1.5M6.5 5.5 8 4a1.5 1.5 0 0 0-2-2L4.5 3.5" fill="none" stroke="var(--icon)" stroke-width="1.1" stroke-linecap="round"/></svg></span>
    <span><svg width="10" height="10"><circle cx="2" cy="5" r="1.5" fill="var(--icon)"/><circle cx="8" cy="2" r="1.5" fill="var(--icon)"/><circle cx="8" cy="8" r="1.5" fill="var(--icon)"/><path d="M2 5l6-3M2 5l6 3" stroke="var(--icon)" stroke-width=".9"/></svg></span>
  </div>
</article>

<!-- Post 2 -->
<article>
  <div class="abs post-img" style="left:147px;top:1254px;background:linear-gradient(100deg,#6b4a34 0%,#c9b7a6 20%,#f1ece6 45%,#d9cfc6 70%,#a99a8e 100%)" role="img" aria-label="Photo of a thoughtful woman sitting on a bed by a window"></div>
  <div class="abs post-date" style="left:147px;top:1580px">18 march, 2017</div>
  <h3 class="abs post-title" style="left:147px;top:1608px">Nam tincidunt at arcu ut congue. Sed consectetur dictum ultrices. Mauris vitae nisi nec ipsum malesuada egestas ac ac augue.</h3>
  <div class="abs meta" style="left:147px;top:1672px">
    <span><svg width="9" height="8"><path d="M1 1h7v4H4L2 7V5H1z" fill="#555"/></svg>25 Comments</span>
    <span><svg width="9" height="8"><path d="M4.5 7.5 1 4A2 2 0 0 1 4.5 1.5 2 2 0 0 1 8 4z" fill="#555"/></svg>83 Likes</span>
    <span><svg width="9" height="9"><path d="M1 1h4l3 3-4 4-3-3z" fill="#555"/></svg>Aliquam rhoncus luctus placerat. Duis posuere, ante ut vestibulum</span>
  </div>
  <p class="abs excerpt" style="left:147px;top:1696px">Proin rutrum, velit vitae pharetra cursus, mauris diam tempor libero, ut rhoncus massa lacus vel lectus. Pellentesque et nisl ac orci rhoncus porta quis in tortor. Nunc commodo diam id tristique mollis. Praesent non aliquet sem. Nulla eu vestibulum nunc. In gravida, risus in ultricies condimentum, lacus purus mattis augue.</p>
  <div class="abs share" style="left:147px;top:1764px">
    <span><svg width="10" height="9"><path d="M1 1h8v6H1z" fill="none" stroke="var(--icon)" stroke-width="1.2"/><path d="M1 1l4 3 4-3" fill="none" stroke="var(--icon)" stroke-width="1.2"/></svg></span>
    <span><svg width="10" height="9"><path d="M1 1h8v5H4L2 8V6H1z" fill="none" stroke="var(--icon)" stroke-width="1.2"/></svg></span>
    <span><svg width="10" height="9"><path d="M5 8.5 1.2 4.7A2 2 0 0 1 5 2a2 2 0 0 1 3.8 2.7z" fill="var(--icon)"/></svg></span>
    <span><svg width="10" height="10"><path d="M5 .5l1.3 2.8 3 .3-2.3 2 .7 3L5 7 2.3 8.6l.7-3-2.3-2 3-.3z" fill="var(--icon)"/></svg></span>
    <span><svg width="10" height="10"><path d="M4 6l2-2M3.5 4.5 2 6a1.5 1.5 0 0 0 2 2l1.5-1.5M6.5 5.5 8 4a1.5 1.5 0 0 0-2-2L4.5 3.5" fill="none" stroke="var(--icon)" stroke-width="1.1" stroke-linecap="round"/></svg></span>
    <span><svg width="10" height="10"><circle cx="2" cy="5" r="1.5" fill="var(--icon)"/><circle cx="8" cy="2" r="1.5" fill="var(--icon)"/><circle cx="8" cy="8" r="1.5" fill="var(--icon)"/><path d="M2 5l6-3M2 5l6 3" stroke="var(--icon)" stroke-width=".9"/></svg></span>
  </div>
</article>

<!-- Post 3 -->
<article>
  <div class="abs post-img" style="left:147px;top:1842px;background:linear-gradient(110deg,#9d5a8a 0%,#e7a08c 35%,#f6e6dc 55%,#b6a5c9 80%,#6a6fa3 100%)" role="img" aria-label="Photo of friends jumping joyfully in splashing water at sunset"></div>
  <div class="abs post-date" style="left:147px;top:2168px">18 march, 2017</div>
  <h3 class="abs post-title" style="left:147px;top:2196px">Nam tincidunt at arcu ut congue. Sed consectetur dictum ultrices. Mauris vitae nisi nec ipsum malesuada egestas ac ac augue.</h3>
  <div class="abs meta" style="left:147px;top:2260px">
    <span><svg width="9" height="8"><path d="M1 1h7v4H4L2 7V5H1z" fill="#555"/></svg>25 Comments</span>
    <span><svg width="9" height="8"><path d="M4.5 7.5 1 4A2 2 0 0 1 4.5 1.5 2 2 0 0 1 8 4z" fill="#555"/></svg>83 Likes</span>
    <span><svg width="9" height="9"><path d="M1 1h4l3 3-4 4-3-3z" fill="#555"/></svg>Aliquam rhoncus luctus placerat. Duis posuere, ante ut vestibulum</span>
  </div>
  <p class="abs excerpt" style="left:147px;top:2284px">Proin rutrum, velit vitae pharetra cursus, mauris diam tempor libero, ut rhoncus massa lacus vel lectus. Pellentesque et nisl ac orci rhoncus porta quis in tortor. Nunc commodo diam id tristique mollis. Praesent non aliquet sem. Nulla eu vestibulum nunc. In gravida, risus in ultricies condimentum, lacus purus mattis augue.</p>
  <div class="abs share" style="left:147px;top:2352px">
    <span><svg width="10" height="9"><path d="M1 1h8v6H1z" fill="none" stroke="var(--icon)" stroke-width="1.2"/><path d="M1 1l4 3 4-3" fill="none" stroke="var(--icon)" stroke-width="1.2"/></svg></span>
    <span><svg width="10" height="9"><path d="M1 1h8v5H4L2 8V6H1z" fill="none" stroke="var(--icon)" stroke-width="1.2"/></svg></span>
    <span><svg width="10" height="9"><path d="M5 8.5 1.2 4.7A2 2 0 0 1 5 2a2 2 0 0 1 3.8 2.7z" fill="var(--icon)"/></svg></span>
    <span><svg width="10" height="10"><path d="M5 .5l1.3 2.8 3 .3-2.3 2 .7 3L5 7 2.3 8.6l.7-3-2.3-2 3-.3z" fill="var(--icon)"/></svg></span>
    <span><svg width="10" height="10"><path d="M4 6l2-2M3.5 4.5 2 6a1.5 1.5 0 0 0 2 2l1.5-1.5M6.5 5.5 8 4a1.5 1.5 0 0 0-2-2L4.5 3.5" fill="none" stroke="var(--icon)" stroke-width="1.1" stroke-linecap="round"/></svg></span>
    <span><svg width="10" height="10"><circle cx="2" cy="5" r="1.5" fill="var(--icon)"/><circle cx="8" cy="2" r="1.5" fill="var(--icon)"/><circle cx="8" cy="8" r="1.5" fill="var(--icon)"/><path d="M2 5l6-3M2 5l6 3" stroke="var(--icon)" stroke-width=".9"/></svg></span>
  </div>
</article>

<div class="abs pager"><span>«</span><span>‹</span><span class="active">1</span><span>2</span><span>3</span><span>4</span><span>5</span><span>›</span><span>»</span></div>

<!-- Sidebar -->
<h2 class="abs heading" style="left:828px;top:624px">About Maya</h2>
<p class="abs side-text" style="left:828px;top:660px">Proin rutrum, velit vitae pharetra cursus, mauris diam tempor libero, ut rhoncus massa lacus vel lectus. Pellentesque et nisl ac orci rhoncus porta quis in tortor. Nunc commodo diam id tristique mollis. Praesent non aliquet sem. Nulla eu vestibulum nunc. In gravida, risus in ultricies condimentum.</p>
<div class="abs" style="left:828px;top:822px;width:58px;height:58px;border-radius:50%;background:linear-gradient(160deg,#f4d58a,#6b7fd0);border:3px solid #fff;box-shadow:0 1px 3px rgba(0,0,0,.15)" role="img" aria-label="Portrait of Maya"></div>
<div class="abs" style="left:903px;top:826px;font-family:'Dancing Script',cursive;font-size:19px;color:#444">Maya</div>
<div class="abs" style="left:903px;top:850px;font-size:9.5px;color:#777">Aliquam rhoncus luctus placerat</div>
<div class="abs side-rule" style="top:922px"></div>

<h2 class="abs heading" style="left:828px;top:952px">Contact</h2>
<div class="abs contact-item" style="left:828px;top:997px"><svg width="8" height="11"><path d="M4 10C1 6 1 5 1 4a3 3 0 0 1 6 0c0 1 0 2-3 6z" fill="#555"/></svg><span>24 Building name, Street name,<br>City - Zipcode</span></div>
<div class="abs contact-item" style="left:828px;top:1045px"><svg width="8" height="11"><rect x="1.5" y="1" width="5" height="9" rx="1" fill="none" stroke="#555"/></svg><span>555 014 2290</span></div>
<div class="abs contact-item" style="left:828px;top:1078px"><svg width="8" height="11"><rect x="1.5" y="1" width="5" height="9" rx="1" fill="none" stroke="#555"/></svg><span>hello@brightpathnotesblog.com</span></div>
<div class="abs side-rule" style="top:1129px"></div>

<h2 class="abs heading" style="left:828px;top:1160px">Popular Posts</h2>
<div class="abs" style="left:828px;top:1204px"><p class="pop-title">Praesent non aliquet sem. Nulla eu vestib ulum nunc. In gravida risus.</p><p class="pop-date">16 march, 2017</p></div>
<div class="abs" style="left:828px;top:1276px"><p class="pop-title">Praesent non aliquet sem. Nulla eu vestib ulum nunc. In gravida risus.</p><p class="pop-date">16 march, 2017</p></div>
<div class="abs" style="left:828px;top:1349px"><p class="pop-title">Praesent non aliquet sem. Nulla eu vestib ulum nunc. In gravida risus.</p><p class="pop-date">16 march, 2017</p></div>
<div class="abs" style="left:828px;top:1422px"><p class="pop-title">Praesent non aliquet sem. Nulla eu vestib ulum nunc. In gravida risus.</p><p class="pop-date">16 march, 2017</p></div>
<div class="abs side-rule" style="top:1513px"></div>

<div class="abs" style="left:883px;top:1554px;width:96px;height:481px;background:linear-gradient(180deg,#2a2a2a 0%,#6d7e8f 20%,#b9cde0 45%,#7a8b63 75%,#3b3f2e 100%)" role="img" aria-label="Vertical sports advertisement banner"></div>

<!-- Footer -->
<div class="abs footer-links">Home &nbsp;&nbsp;|&nbsp;&nbsp; About Maya &nbsp;&nbsp;|&nbsp;&nbsp; Contact</div>
<div class="abs copyright">Copyright © 2017 &nbsp;Company name. &nbsp;All rights reserved.</div>

</body>
</html>
```